Dovin Sound 862 the new wave for sound to enlighten open ears

This is a music recording studio, we need pictures of a booth, random pictures of anything that will draw interest to a recording studio, we just need the website to reflect a music studio recording website. Apply generic information on the site that correlates with most music studio websites up to date. We want the modern style look that will entice eyes across the nation. Information should be easily accessible on the website. Dovin Sound 862 is owned by Marcellus Okafor located 5176 Bellweather Ln, Miramar, Fl, 33027. Email: Mokaforsound@trellomail.net and best contact number to date is 417-293-7041. The sound coming out of this location will be radio ready at all times, artist come in one way and come out with more wisdom than before. Its the new way to make music the appropriate way and bring the best out of those willing to reach their peak.

Target Market(s)

Recording Artist

Industry/Entity Type

Recording Studio

Coding

Coded - Design and coding required

Number of Pages Required

1 page

Font styles to use
Sans Serif

Requirements
Must have
• Anything that gives the site a music feel
Nice to have
• microphones, booths, studio mixing desk

```html
<!DOCTYPE html>
<html lang="en">
<head>
<meta charset="utf-8">
<title>Dovin Sound 862 — Music Recording Studio</title>
<link rel="stylesheet" href="https://fonts.googleapis.com/css2?family=Raleway:wght@500;600;700;800&family=Open+Sans:wght@400;600&display=swap">
<style>
:root{
  --red:#cf2f26;
  --red-deep:#a8231b;
  --ink:#3b3b3b;
  --text:#8a8a8a;
  --muted:#a5a5a5;
  --gold:#f6b21b;
  --white:#ffffff;
  --rule:#ececec;
  --band:#1f1f1f;
}
*{box-sizing:border-box;margin:0;padding:0}
html,body{width:1200px;height:3321px;overflow:hidden;background:var(--white)}
body{position:relative;font-family:"Open Sans",Arial,sans-serif;color:var(--ink)}
.abs{position:absolute}
.heading{font-family:"Raleway",Arial,sans-serif;font-weight:700;letter-spacing:2px;text-transform:uppercase}
.center{left:0;width:1200px;text-align:center}
.accent-line{width:34px;height:3px;background:var(--red);left:583px}

/* header */
.site-header{top:0;left:0;width:1200px;height:71px;background:var(--white)}
.brand{left:100px;top:18px;font-family:"Raleway",sans-serif;font-weight:700;font-size:27px;letter-spacing:1px;color:var(--red);text-transform:uppercase}
.nav a{position:absolute;top:29px;font-family:"Raleway",sans-serif;font-size:12px;font-weight:500;color:#6d6d6d;text-decoration:none;text-transform:uppercase;letter-spacing:.5px}

/* hero */
.hero{top:71px;left:0;width:1200px;height:551px;background:linear-gradient(180deg,#2a1d15 0%,#4a3222 45%,#5b3a22 70%,#2b1c12 100%)}
.hero-shade{inset:0;background:rgba(0,0,0,.25)}
.hero-title{top:185px;font-family:"Raleway",sans-serif;font-weight:600;font-size:48px;letter-spacing:4px;color:var(--white)}
.hero-sub{top:252px;font-family:"Raleway",sans-serif;font-weight:500;font-size:20px;letter-spacing:2px;color:var(--white)}
.hero-btn{top:307px;left:524px;width:154px;height:36px;border-radius:18px;background:var(--red);color:var(--white);font-family:"Raleway",sans-serif;font-weight:700;font-size:12px;letter-spacing:1px;line-height:36px;text-align:center}
.hero-arrow{top:253px;width:40px;height:40px;border:1px solid rgba(255,255,255,.35);border-radius:50%}

/* section headings */
.section-title{font-size:17px;color:#454545}
.lead{left:232px;width:736px;text-align:center;font-size:13px;line-height:27px;color:var(--muted)}

/* works grid */
.work{width:300px}
.work-photo{height:200px}
.work-title{font-family:"Raleway",sans-serif;font-weight:700;font-size:13px;letter-spacing:1px;color:#6b6b6b;text-align:center;margin-top:22px}
.work-link{font-size:10px;color:#8f8f8f;text-align:center;margin-top:4px}
.outline-btn{left:516px;width:168px;height:40px;border:1px solid var(--red);border-radius:20px;color:var(--red);font-family:"Raleway",sans-serif;font-weight:600;font-size:11px;letter-spacing:.5px;line-height:38px;text-align:center;text-transform:uppercase;background:var(--white)}

/* sessions */
.sessions{top:1722px;left:0;width:1200px;height:368px;background:linear-gradient(90deg,#141414 0%,#2c2c2c 40%,#3a3a3a 70%,#1d1d1d 100%)}
.price-col{top:89px;width:300px;color:var(--white)}
.price-col h3{font-family:"Raleway",sans-serif;font-weight:700;font-size:18px;letter-spacing:1.5px;margin-bottom:20px}
.price-col p{font-size:12px;line-height:18px;margin-bottom:20px;color:#eee}
.price-col .rate{color:var(--gold);font-size:18px;font-weight:600;margin-right:2px}
.price-col .deal{margin-bottom:12px}

/* blog */
.post{width:470px}
.post h4{font-family:"Raleway",sans-serif;font-weight:700;font-size:13px;letter-spacing:1px;color:#5b5b5b;margin-bottom:14px}
.post p{font-size:12.5px;line-height:25px;color:var(--muted)}

/* about */
.about{top:2615px;left:0;width:1200px;height:385px;background:linear-gradient(100deg,#b52a20 0%,#a8231b 50%,#8f1e17 100%)}
.about .heading{color:var(--white)}
.about-text{left:210px;width:780px;text-align:center;font-size:11.5px;line-height:24px;color:#fbe5e3}
.about-btn{left:516px;width:168px;height:40px;border:1px solid var(--white);border-radius:20px;color:var(--white);font-family:"Raleway",sans-serif;font-weight:600;font-size:11px;line-height:38px;text-align:center;text-transform:uppercase}

/* footer */
.footer-col{top:3053px}
.footer-col h5{font-family:"Raleway",sans-serif;font-weight:700;font-size:15px;letter-spacing:1.5px;color:#505050;text-transform:uppercase}
.footer-col .bar{width:34px;height:2px;background:var(--red);margin:11px 0 16px}
.footer-col li{list-style:none;font-size:11.5px;color:#777;height:24px;display:flex;align-items:center;gap:10px}
.footer-col li svg{flex:none}
.social{display:flex;gap:7px;margin-top:10px}
.social span{width:33px;height:33px;border-radius:50%}
.footer-rule{top:3259px;left:0;width:1200px;height:1px;background:var(--rule)}
.copyright{top:3281px;font-size:11px;color:#888}
</style>
</head>
<body>

<header class="abs site-header">
  <div class="abs brand">Dovin Sound 862</div>
  <nav class="nav">
    <a style="left:664px">Home</a>
    <a style="left:751px">Work</a>
    <a style="left:837px">About Us</a>
    <a style="left:941px">Sessions</a>
    <a style="left:1045px">Contact</a>
  </nav>
</header>

<section class="abs hero" role="img" aria-label="Recording studio control room with a large mixing console and monitor speakers">
  <div class="abs hero-shade"></div>
  <h1 class="abs center hero-title">DOVIN SOUND 862</h1>
  <p class="abs center hero-sub">WE ARE A MUSIC RECORDING STUDIO</p>
  <div class="abs hero-btn">SEND EMAIL</div>
  <div class="abs hero-arrow" style="left:38px"><svg width="40" height="40" viewBox="0 0 40 40"><path d="M23 13l-7 7 7 7" fill="none" stroke="#fff" stroke-opacity=".6" stroke-width="1.5"/></svg></div>
  <div class="abs hero-arrow" style="left:1122px"><svg width="40" height="40" viewBox="0 0 40 40"><path d="M17 13l7 7-7 7" fill="none" stroke="#fff" stroke-opacity=".6" stroke-width="1.5"/></svg></div>
</section>

<h2 class="abs center heading section-title" style="top:694px">Welcome to Dovin Sound 862</h2>
<div class="abs accent-line" style="top:736px"></div>
<p class="abs lead" style="top:767px">Lorem Ipsum is simply dummy text of the printing and typesetting industry. Lorem Ipsum has been the industry's standard dummy text ever since the 1500s, when an unknown printer took a galley of type and scrambled it to make a type specimen book. It has survived not only five centuries, but also the leap into electronic...</p>

<h2 class="abs center heading section-title" style="top:904px">Music Studio Recording</h2>
<div class="abs accent-line" style="top:940px"></div>

<div class="abs work" style="top:983px;left:0">
  <div class="work-photo" role="img" aria-label="Singer wearing headphones in warm sunlight" style="background:linear-gradient(135deg,#e9b86a,#6b5a52 60%,#2f2a2a)"></div>
  <div class="work-title">LOREM IPSUM IS SIMPLY</div><div class="work-link">( www.samplereel.net/video )</div>
</div>
<div class="abs work" style="top:983px;left:300px">
  <div class="work-photo" role="img" aria-label="Hands playing a hand drum" style="background:linear-gradient(135deg,#3a3a3a,#8f8a82 50%,#2a2a2a)"></div>
  <div class="work-title">LOREM IPSUM IS SIMPLY</div><div class="work-link">( www.samplereel.net/video )</div>
</div>
<div class="abs work" style="top:983px;left:600px">
  <div class="work-photo" role="img" aria-label="Performer on a night stage with city lights" style="background:linear-gradient(160deg,#1a2230,#3c4d66 55%,#0f1520)"></div>
  <div class="work-title">LOREM IPSUM IS SIMPLY</div><div class="work-link">( www.samplereel.net/video )</div>
</div>
<div class="abs work" style="top:983px;left:900px">
  <div class="work-photo" role="img" aria-label="Guitarist on stage under purple light" style="background:linear-gradient(135deg,#2a1030,#8a4a8a 55%,#e6c0d8)"></div>
  <div class="work-title">LOREM IPSUM IS SIMPLY</div><div class="work-link">( www.samplereel.net/video )</div>
</div>

<div class="abs work" style="top:1255px;left:0">
  <div class="work-photo" role="img" aria-label="Brass players performing outdoors" style="background:linear-gradient(135deg,#f1e4c2,#c9a56a 55%,#5e4a33)"></div>
  <div class="work-title">LOREM IPSUM IS SIMPLY</div><div class="work-link">( www.samplereel.net/video )</div>
</div>
<div class="abs work" style="top:1255px;left:300px">
  <div class="work-photo" role="img" aria-label="Band rehearsing together in a room" style="background:linear-gradient(135deg,#d89b3a,#8a5a2f 50%,#4a3020)"></div>
  <div class="work-title">LOREM IPSUM IS SIMPLY</div><div class="work-link">( www.samplereel.net/video )</div>
</div>
<div class="abs work" style="top:1255px;left:600px">
  <div class="work-photo" role="img" aria-label="DJ turntables lit in orange" style="background:linear-gradient(135deg,#2a1408,#d07a1c 55%,#f2b440)"></div>
  <div class="work-title">LOREM IPSUM IS SIMPLY</div><div class="work-link">( www.samplereel.net/video )</div>
</div>
<div class="abs work" style="top:1255px;left:900px">
  <div class="work-photo" role="img" aria-label="Hands on a mixing desk with green meters" style="background:linear-gradient(135deg,#1a1f1a,#3a4a3a 55%,#5e8a3a)"></div>
  <div class="work-title">LOREM IPSUM IS SIMPLY</div><div class="work-link">( www.samplereel.net/video )</div>
</div>

<div class="abs outline-btn" style="top:1554px">View More Works</div>

<h2 class="abs center heading section-title" style="top:1648px">Sessions</h2>
<div class="abs accent-line" style="top:1686px"></div>

<section class="abs sessions" role="img" aria-label="Dark close-up of studio mixing faders as background">
  <div class="abs price-col" style="left:100px">
    <h3>RECORDING PRICE</h3>
    <p><span class="rate">$80</span> per hour minimum 4 hours required</p>
    <p><span class="rate">$75</span> per hour minimum 8 hours required</p>
    <p><span class="rate">$70</span> per hour minimum 12 hours required</p>
    <p><span class="rate">$90</span> for individual hours, packages recom-<br>mende</p>
  </div>
  <div class="abs price-col" style="left:463px">
    <h3>MEMBERSHIPS DEALS</h3>
    <p class="deal"><span class="rate">$1500</span> get 48 recording hours in addition to<br>24 hours mix down</p>
    <p class="deal"><span class="rate">$2500</span> get 72 recording hours in addition to<br>48 hours mix down</p>
    <p class="deal"><span class="rate">$3500</span> get 96 recording hours in addition to<br>72 hours mix down</p>
  </div>
  <div class="abs price-col" style="left:828px">
    <h3>MIX DOWN ONLY PRICES</h3>
    <p><span class="rate">$50</span> per hour minimum 4 hours required</p>
    <p><span class="rate">$45</span> per hour minimum 8 hours required</p>
    <p><span class="rate">$40</span> per hour minimum 12 hours required</p>
    <p><span class="rate">$60</span> for individual hours, packages recom-<br>mended</p>
  </div>
</section>

<h2 class="abs center heading section-title" style="top:2166px">Blog Posts</h2>
<div class="abs accent-line" style="top:2204px"></div>

<article class="abs post" style="top:2260px;left:100px"><h4>LOREM IPSUM IS SIMPLY DUMMY TEXT</h4><p>Lorem Ipsum is simply dummy text of the printing and typesetting industry. Lorem Ipsum has been the industry</p></article>
<article class="abs post" style="top:2260px;left:613px"><h4>LOREM IPSUM IS SIMPLY DUMMY TEXT</h4><p>Lorem Ipsum is simply dummy text of the printing and typesetting industry. Lorem Ipsum has been the industry</p></article>
<article class="abs post" style="top:2382px;left:100px"><h4>LOREM IPSUM IS SIMPLY DUMMY TEXT</h4><p>Lorem Ipsum is simply dummy text of the printing and typesetting industry. Lorem Ipsum has been the industry</p></article>
<article class="abs post" style="top:2382px;left:613px"><h4>LOREM IPSUM IS SIMPLY DUMMY TEXT</h4><p>Lorem Ipsum is simply dummy text of the printing and typesetting industry. Lorem Ipsum has been the industry</p></article>

<div class="abs outline-btn" style="top:2504px">View More Posts</div>

<section class="abs about" role="img" aria-label="Red-tinted studio headphones and mixing desk as background">
  <h2 class="abs center heading section-title" style="top:94px;color:#fff">About Dovin Sound 862</h2>
  <div class="abs accent-line" style="top:130px;background:#fff"></div>
  <p class="abs about-text" style="top:158px">Lorem Ipsum is simply dummy text of the printing and typesetting industry. Lorem Ipsum has been the industry's standard dummy text ever since the 1500s, when an unknown printer took a galley of type and scrambled it to make a type specimen book. It has survived not only five centuries, but also the leap into electronic typesetting, remaining essentially unchanged.</p>
  <div class="abs about-btn" style="top:252px">View More Details</div>
</section>

<div class="abs footer-col" style="left:100px">
  <h5>Welcome</h5><div class="bar"></div>
  <ul><li>Home</li><li>Work</li><li>About Us</li><li>Sessions</li><li>Contact</li></ul>
</div>
<div class="abs footer-col" style="left:312px">
  <h5>Information</h5><div class="bar"></div>
  <ul><li>Terms &amp; Conditions</li><li>Privacy Policy</li><li>Disclaimer</li><li>Sitemap</li></ul>
</div>
<div class="abs footer-col" style="left:560px">
  <h5>Contact Info</h5><div class="bar"></div>
  <ul>
    <li><svg width="10" height="13" viewBox="0 0 10 13"><path d="M5 0a5 5 0 0 0-5 5c0 3.5 5 8 5 8s5-4.5 5-8a5 5 0 0 0-5-5zm0 7a2 2 0 1 1 0-4 2 2 0 0 1 0 4z" fill="#cf2f26"/></svg>5176 Bellweather Ln, Miramar, Fl, 33027</li>
    <li><svg width="12" height="9" viewBox="0 0 12 9"><rect x=".5" y=".5" width="11" height="8" fill="none" stroke="#cf2f26"/><path d="M.5.5L6 5l5.5-4.5" fill="none" stroke="#cf2f26"/></svg>Email: Mokaforsound@trellomail.net</li>
    <li><svg width="11" height="11" viewBox="0 0 11 11"><path d="M2.2 0L4 2.6 2.9 4a6.5 6.5 0 0 0 4.1 4.1L8.4 7 11 8.8 9.6 11C4.3 10.8.2 6.7 0 1.4z" fill="#cf2f26"/></svg>Phone 417-293-7041</li>
  </ul>
</div>
<div class="abs footer-col" style="left:877px">
  <h5>Follow Us</h5><div class="bar"></div>
  <ul><li>Connect with our social network</li></ul>
  <div class="social">
    <span style="background:#2f5ea8"></span>
    <span style="background:#1e86b5"></span>
    <span style="background:#f0a028"></span>
    <span style="background:#39b4e6"></span>
    <span style="background:#d8261f"></span>
  </div>
</div>

<div class="abs footer-rule"></div>
<p class="abs center copyright">© 2017. Dovin Sound 862. All Rights Reserved</p>

</body>
</html>
```